business card design for a plumbing contractor

i need a double business card for a plumbing business, our initial service is residential Sewer Drain Cleaning.

Target Market(s)

other plumbing Business

Industry/Entity Type

Plumbing

Contact Information for Business Card

www.PipeworksTopMark.example- 5307218394-

Font styles to use
Serif

Colors
ec1f27
0455a3

```html
<!DOCTYPE html>
<html lang="en">
<head>
<meta charset="utf-8">
<title>Pipeworks Top Mark – Business Card</title>
<link rel="stylesheet" href="https://fonts.googleapis.com/css2?family=Roboto+Condensed:wght@400;700&family=Roboto:wght@400&display=swap">
<style>
  :root {
    --stage: #2b2b2b;
    --card-light: #f1f1f1;
    --brand-red: #d6382e;
    --name-red: #d9322a;
    --taupe: #7b7565;
    --ink: #4a4a4a;
    --white: #ffffff;
  }
  * { margin: 0; padding: 0; box-sizing: border-box; }
  html, body {
    width: 1200px; height: 960px; overflow: hidden;
    background: var(--stage);
    font-family: "Roboto Condensed", Arial, sans-serif;
  }
  .card {
    position: absolute; width: 600px; height: 343px;
    box-shadow: 0 3px 8px rgba(0,0,0,.45);
    overflow: hidden;
  }
  .card--front { left: 322px; top: 108px; background: var(--card-light); }
  .card--back  { left: 320px; top: 493px; background: var(--brand-red); }

  .brand-mark-area {
    position: absolute; left: 30px; top: 62px;
    width: 230px; height: 230px;
    background: var(--brand-red);
  }

  .front-brand {
    position: absolute; right: 32px; top: 34px;
  }
  .front-brand__name {
    font-weight: 700; font-size: 42px; line-height: 42px;
    color: var(--taupe); text-align: right;
  }

  .contact {
    position: absolute; right: 27px; top: 210px; text-align: right;
  }
  .contact__name { color: var(--name-red); font-size: 22px; line-height: 26px; }
  .contact__role { color: var(--taupe); font-size: 15px; line-height: 18px; margin-bottom: 12px; letter-spacing: .3px; }
  .contact__line { color: var(--ink); font-size: 14px; line-height: 18px; }

  .back-brand {
    position: absolute; left: 0; right: 0; top: 126px;
    display: flex; justify-content: center; align-items: center; gap: 16px;
  }
  .back-brand__name {
    color: var(--white); font-weight: 700; font-size: 38px; line-height: 38px;
  }
  .back-brand__square { width: 34px; height: 34px; background: var(--white); }
  .services {
    position: absolute; left: 0; right: 0; top: 283px;
    text-align: center; color: var(--white);
    font-family: "Roboto", Arial, sans-serif; font-size: 15px;
  }
</style>
</head>
<body>
  <section class="card card--front">
    <div class="brand-mark-area" role="img" aria-label="Large brand symbol area"></div>
    <div class="front-brand">
      <div class="front-brand__name">Pipeworks<br>Top Mark</div>
    </div>
    <div class="contact">
      <div class="contact__name">DANA WHITFIELD</div>
      <div class="contact__role">CEO/FOUNDER</div>
      <div class="contact__line">(P) 5307218394</div>
      <div class="contact__line">Dispatch@PipeworksTopMark.example</div>
      <div class="contact__line">www.PipeworksTopMark.example</div>
    </div>
  </section>

  <section class="card card--back">
    <div class="back-brand">
      <div class="back-brand__name">Pipeworks<br>Top Mark</div>
      <div class="back-brand__square"></div>
    </div>
    <div class="services">Sewer Drain Cleaning • Maintenance • Trenchless Pipe Installs</div>
  </section>
</body>
</html>
```